Fitness Equipment & Service

I want to make the card eye catching and fun. We are called Corvane Motion Limited and we are based in Wales. We sell, install and service all types of fitness equipment from Skipping ropes, right through the Dumbbells, Kettle bells and Barbells through to state of the art Treadmills, Running Machines and Strength Equipment. We also design and install changing room furniture and lockers.

TYPOGRAPHY
We would like to use Futrura. Futura has an appearance of efficiency and forwardness. The typeface is derived
from simple geometric forms (near-perfect circles, triangles and squares) and is based on strokes of
near-even weight, which are low in contrast. This is most visible in the almost perfectly round stroke of
the o, which is nonetheless slightly ovoid.
The lowercase has tall ascenders, which rise above the cap line. The uppercase
characters present proportions similar to those of classical Roman capitals.

TYPOGRAPHIC CONSIDERATIONS
No Strike though
No Horizontal Scaling
No Drop Shadows
No Effects
Never use less than 120% Leading

OUR CORPORATE COLOURS
BRAND GUIDELINES
We were thinking that our primary colour palette consists of the Acid Green (Pantone 382) and Process Black.

We work closely with tquarly Ltd and would like to include their name on the card somewhere. I have attached images of the other brands that we work with as an idea or the small icons I have included that illustrate what we do?. I have very kindly been given permission to use any of the images off the files that I have included below, so I hope these help. I will include these below. I would be open to suggestions if it made the card more striking Can you do it?
Updates

Hi All, Just wanted to add a few thoughts but you are the guys with the creative visions (thats why are here) We are based in Wales, UK and we would be open to lots of different ideas on a theme but must be eye catching, Bold and FUN. If you can or think that the Welsh or any dragon could be put in there then go for it (its not a must have) We have also added some ideas for colour but again its over to you!! GO FOR IT ! Thanks and look forward to your visions! Owen

Hi All, Just thought I would sen through the contact details that need to be on the card. (if you want to play around with icons instead of the wording twitter, Facebook, go for it): Corvane Motion Limited Owen Pritchard Managing Director Mob: +44 (0)7582 913 406 e-mail: sales@corvanemotion.co.uk Web: Corvanemotion.co.uk twitter: @motionLetterbin Facebook: Corvane Motion Limited

```html
<!DOCTYPE html>
<html lang="en">
<head>
<meta charset="utf-8">
<title>Corvane Motion Limited – Business Card</title>
<link rel="stylesheet" href="https://fonts.googleapis.com/css2?family=Jost:wght@500;600&display=swap">
<style>
  :root {
    --backdrop: #e9e6e1;
    --card-white: #ffffff;
    --navy: #241a5c;
    --gold: #d8b862;
    --blue-deep: #0f4f8f;
    --blue-mid: #1f7fc6;
    --blue-light: #46c2e6;
    --ink-white: #ffffff;
  }
  * { box-sizing: border-box; margin: 0; padding: 0; }
  html, body {
    width: 1200px; height: 892px; overflow: hidden;
    background: var(--backdrop);
    font-family: "Jost", "Futura", sans-serif;
  }
  .canvas {
    position: relative; width: 1200px; height: 892px;
    display: flex; justify-content: center; align-items: center; gap: 100px;
  }
  .card {
    position: relative; width: 400px; height: 680px;
    border-radius: 22px; overflow: hidden;
    box-shadow: 0 6px 24px rgba(0,0,0,0.18);
  }

  /* Front */
  .card-front { background: var(--card-white); }
  .brand-mark {
    position: absolute; left: 50%; top: 60px; transform: translateX(-50%);
    width: 150px; height: 150px; border-radius: 50%;
    background: radial-gradient(circle at 40% 35%, #5a4fc4, var(--navy));
  }
  .brand-name {
    position: absolute; left: 0; right: 0; top: 246px;
    text-align: center; font-weight: 600; font-size: 30px; line-height: 1.2;
    color: var(--navy);
  }
  .contact-list { position: absolute; left: 0; right: 0; top: 340px; list-style: none; }
  .contact-row { position: relative; height: 52px; margin-bottom: 8px; }
  .contact-icon {
    position: absolute; left: 14px; top: 12px; width: 28px; height: 28px;
    border-radius: 4px; background: var(--navy);
    display: flex; align-items: center; justify-content: center;
  }
  .contact-icon svg { width: 18px; height: 18px; }
  .contact-band {
    position: absolute; left: 52px; right: 0; top: 0; bottom: 0;
    display: flex; align-items: center; padding-left: 18px;
    font-weight: 500; font-size: 21px; line-height: 1.2;
  }
  .band-gold { background: var(--gold); color: var(--navy); }
  .band-navy { background: var(--navy); color: var(--gold); }

  /* Back */
  .card-back { background: var(--blue-deep); }
  .tile-field {
    position: absolute; inset: 0;
    background: linear-gradient(135deg, var(--blue-light) 0%, var(--blue-mid) 45%, var(--blue-deep) 100%);
  }
  .back-name {
    position: absolute; left: 50%; top: 50%;
    transform: translate(-50%, -50%) rotate(90deg);
    white-space: nowrap; font-weight: 600; font-size: 40px; line-height: 1.2;
    color: var(--ink-white); letter-spacing: 1px;
  }
</style>
</head>
<body>
<main class="canvas">
  <section class="card card-front" aria-label="Card front">
    <div class="brand-mark"></div>
    <h1 class="brand-name">Corvane Motion Limited</h1>
    <ul class="contact-list">
      <li class="contact-row">
        <span class="contact-icon" aria-hidden="true"></span>
        <span class="contact-band band-gold">@motionLetterbin</span>
      </li>
      <li class="contact-row">
        <span class="contact-icon" aria-hidden="true">
          <svg viewBox="0 0 24 24"><path fill="#fff" d="M6.6 10.8a15 15 0 0 0 6.6 6.6l2.2-2.2a1 1 0 0 1 1-.25 11.4 11.4 0 0 0 3.6.57 1 1 0 0 1 1 1V20a1 1 0 0 1-1 1A17 17 0 0 1 3 4a1 1 0 0 1 1-1h3.5a1 1 0 0 1 1 1c0 1.25.2 2.45.57 3.57a1 1 0 0 1-.25 1z"/></svg>
        </span>
        <span class="contact-band band-navy">+44 (0)7582 913 406</span>
      </li>
      <li class="contact-row">
        <span class="contact-icon" aria-hidden="true">
          <svg viewBox="0 0 24 24"><circle cx="12" cy="12" r="9" fill="none" stroke="#fff" stroke-width="2"/><path d="M3 12h18M12 3c3 3 3 15 0 18M12 3c-3 3-3 15 0 18" fill="none" stroke="#fff" stroke-width="1.5"/></svg>
        </span>
        <span class="contact-band band-gold">Corvanemotion.co.uk</span>
      </li>
      <li class="contact-row">
        <span class="contact-icon" aria-hidden="true"></span>
        <span class="contact-band band-navy">Corvane Motion Limited</span>
      </li>
      <li class="contact-row">
        <span class="contact-icon" aria-hidden="true">
          <svg viewBox="0 0 24 24"><rect x="3" y="6" width="18" height="12" fill="none" stroke="#fff" stroke-width="2"/><path d="M3 6l9 7 9-7" fill="none" stroke="#fff" stroke-width="2"/></svg>
        </span>
        <span class="contact-band band-gold">sales@corvanemotion.co.uk</span>
      </li>
    </ul>
  </section>

  <section class="card card-back" aria-label="Card back">
    <div class="tile-field" role="img" aria-label="Blue tiled panel with fitness equipment icons and a gym weight plate"></div>
    <p class="back-name">Corvane Motion Limited</p>
  </section>
</main>
</body>
</html>
```